Business Card for Field Lotus-Eco Friendly Organic Clothing Brand

We are looking for an amazing business card for our eco friendly, organic clothing brand. We are thinking maybe a business card with a peel off sticker on the back, since our hanging clothing tag is a peel off sticker on the back. I will attach our hang tag so we can make sure we stay in line with our design. I've also attached a bag we are doing because I do like the scattered emblem look as well.

```html
<!DOCTYPE html>
<html lang="en">
<head>
<meta charset="utf-8">
<title>Field Lotus Business Card</title>
<link href="https://fonts.googleapis.com/css2?family=Arimo:wght@400;700&family=Cormorant+Garamond:ital,wght@1,600&display=swap" rel="stylesheet">
<style>
  :root {
    --bg: #ece8e1;
    --card-white: #ffffff;
    --forest: #1f2a1c;
    --gold: #c9a13a;
    --gold-light: #e8cf7e;
    --ink: #222222;
    --silver: #a9a9a7;
    --silver-light: #d2d2cf;
  }
  * { margin: 0; padding: 0; box-sizing: border-box; }
  html, body { width: 1200px; height: 892px; overflow: hidden; background: var(--bg); }
  body { position: relative; font-family: "Arimo", Arial, sans-serif; }

  .card {
    position: absolute; left: 320px; width: 560px; height: 320px;
    border-radius: 4px; overflow: hidden;
    box-shadow: 0 6px 18px rgba(0,0,0,0.18);
  }
  .card--front { top: 96px; background: var(--card-white); }
  .card--back { top: 476px; }

  .front-swoosh { position: absolute; inset: 0; }

  .logo-panel {
    position: absolute; left: 250px; top: 30px; width: 220px; height: 112px;
    background: var(--forest); border: 3px solid var(--gold); border-radius: 12px;
  }
  .logo-figure {
    position: absolute; left: 14px; top: 16px; width: 74px; height: 74px;
    border: 2px solid var(--gold);
    background: linear-gradient(135deg, #6b6a3e, #c9a13a 55%, #4b4a2c);
  }
  .logo-name {
    position: absolute; left: 100px; top: 30px;
    color: var(--gold); font-weight: 700; font-size: 22px; line-height: 1.1;
  }
  .logo-url {
    position: absolute; left: 100px; top: 84px;
    color: var(--silver-light); font-size: 9px;
  }

  .contact-list { position: absolute; left: 36px; top: 74px; list-style: none; }
  .contact-item {
    display: flex; align-items: center; gap: 10px;
    font-size: 14px; color: var(--ink); margin-bottom: 9px;
  }
  .contact-icon {
    width: 16px; height: 16px; background: var(--forest); border-radius: 2px;
    display: flex; align-items: center; justify-content: center;
  }

  .person { position: absolute; right: 40px; top: 172px; text-align: right; }
  .person-name { color: var(--gold); font-weight: 700; font-size: 30px; }
  .person-title { color: var(--ink); font-size: 15px; margin-top: 2px; }

  .sticker-swatch {
    position: absolute; left: 300px; top: 238px; width: 100px; height: 66px;
    border-radius: 4px;
    background: linear-gradient(135deg, #2a3324, #4a4a2e 50%, #2a3324);
    outline: 1px solid var(--gold); outline-offset: 3px;
  }

  .back-pattern {
    position: absolute; inset: 0;
    background: linear-gradient(135deg, var(--silver-light), var(--silver) 50%, #bdb9a8);
  }
  .back-frame {
    position: absolute; left: 80px; top: 78px; width: 400px; height: 164px;
    background: var(--forest); border-radius: 18px; padding: 12px;
  }
  .back-frame-inner {
    width: 100%; height: 100%;
    border: 3px solid var(--gold); border-radius: 10px;
    background: #bfbdb7;
    display: flex; align-items: center; justify-content: space-around; padding: 0 24px;
  }
  .back-figure {
    width: 72px; height: 90px; border-radius: 6px;
    background: linear-gradient(135deg, #6b6a3e, #c9a13a 55%, #4b4a2c);
  }
  .back-group { display: flex; flex-direction: column; align-items: center; gap: 8px; }
  .back-word {
    font-family: "Cormorant Garamond", Georgia, serif; font-style: italic; font-weight: 600;
    color: var(--gold-light); font-size: 38px; line-height: 1;
  }
  .back-icons { display: flex; gap: 26px; align-items: center; }
</style>
</head>
<body>

<section class="card card--front" aria-label="Card front">
  <svg class="front-swoosh" width="560" height="320" viewBox="0 0 560 320" aria-hidden="true">
    <path d="M0 186 C120 196 190 270 310 282 C370 288 410 300 430 320 L0 320 Z" fill="var(--forest)"/>
    <path d="M0 172 C130 182 200 258 315 270 C380 276 420 292 445 320" fill="none" stroke="var(--gold)" stroke-width="5"/>
  </svg>

  <div class="logo-panel">
    <div class="logo-figure" role="img" aria-label="Camouflage-patterned meditating figure emblem"></div>
    <div class="logo-name">Field<br>Lotus</div>
    <div class="logo-url">www.fieldlotus.com</div>
  </div>

  <ul class="contact-list">
    <li class="contact-item">
      <span class="contact-icon"><svg width="10" height="10" viewBox="0 0 10 10"><path d="M2 1 L4 1 L4.5 3 L3.5 4 C4 5.5 5 6.5 6 6.8 L7 5.8 L9 6.3 L9 8.5 C5 9 1 5 1.5 1.5 Z" fill="#fff"/></svg></span>
      (555) 014-2290
    </li>
    <li class="contact-item">
      <span class="contact-icon"><svg width="10" height="10" viewBox="0 0 10 10"><path d="M5 0.5 C7.2 0.5 8.5 2 8.5 3.8 C8.5 6 5 9.5 5 9.5 C5 9.5 1.5 6 1.5 3.8 C1.5 2 2.8 0.5 5 0.5 Z" fill="#fff"/><circle cx="5" cy="3.8" r="1.3" fill="var(--forest)"/></svg></span>
      Palm Cove, FL 33000
    </li>
    <li class="contact-item">
      <span class="contact-icon"><svg width="10" height="10" viewBox="0 0 10 10"><rect x="1" y="2.5" width="8" height="5.5" fill="#fff"/><path d="M1 2.5 L5 5.5 L9 2.5" fill="none" stroke="var(--forest)" stroke-width="0.8"/></svg></span>
      hello@fieldlotus.com
    </li>
  </ul>

  <div class="sticker-swatch" role="img" aria-label="Peel-off sticker with scattered namaste, love and peace word pattern"></div>

  <div class="person">
    <div class="person-name">Dana Rivers</div>
    <div class="person-title">President</div>
  </div>
</section>

<section class="card card--back" aria-label="Card back">
  <div class="back-pattern" role="img" aria-label="Scattered gold foil pattern of namaste, live, love, peace words and heart and peace icons on silver"></div>
  <div class="back-frame">
    <div class="back-frame-inner">
      <div class="back-figure" role="img" aria-label="Camouflage-patterned meditating figure"></div>
      <div class="back-group">
        <span class="back-word">inspire</span>
        <div class="back-icons">
          <svg width="44" height="40" viewBox="0 0 44 40" aria-label="Heart" role="img"><path d="M22 38 C6 26 1 18 4 10 C7 2 17 2 22 10 C27 2 37 2 40 10 C43 18 38 26 22 38 Z" fill="var(--gold)" stroke="var(--forest)" stroke-width="2"/></svg>
          <svg width="40" height="40" viewBox="0 0 40 40" aria-label="Peace sign" role="img"><circle cx="20" cy="20" r="18" fill="var(--forest)"/><circle cx="20" cy="20" r="14" fill="none" stroke="var(--gold)" stroke-width="3"/><path d="M20 6 L20 34 M20 20 L10 30 M20 20 L30 30" stroke="var(--gold)" stroke-width="3"/></svg>
        </div>
      </div>
    </div>
  </div>
</section>

</body>
</html>
```